Garlic Farm for Farm Sales/Restaurant sales

Need a professional, but appealing to agriculture world. We are selling 27 kinds of Organic Garlic from a farm in Simla,CO. I have uploaded logo and business information-we are going to need a template, because I will need to use it for four separate people.
-We are trying to appeal to Farm to table restaurants
-As well as growers/farmers

Target Market(s)

Agriculture Sales/Restaurants-Organic

Industry/Entity Type

Agriculture

Contact Information for Business Card

Want it to look more unique then your average kelto stock card- I want it to look amazing

Font styles to use
Sans Serif

Colors
0455a3
ec1f27
fbed22
ffffff

Requirements
Must have
• Just be creative
Nice to have
• Colorful
Should not have
• plain

```html
<!DOCTYPE html>
<html lang="en">
<head>
<meta charset="utf-8">
<title>Summit Ridge Garlic – Business Card</title>
<link rel="stylesheet" href="https://fonts.googleapis.com/css2?family=Kalam:wght@400;700&family=Questrial&display=swap">
<style>
  :root {
    --navy: #16204a;
    --navy-deep: #0d1535;
    --gold: #e8b40f;
    --gold-light: #fbd022;
    --red: #c8202a;
    --card-white: #f3f2ef;
    --text-light: #e6e6ea;
    --page: #dcdcdf;
  }
  html, body {
    margin: 0;
    width: 1200px;
    height: 969px;
    overflow: hidden;
    background: var(--page);
  }
  .business-card {
    position: absolute;
    left: 100px;
    top: 200px;
    width: 1000px;
    height: 568px;
    border-radius: 24px;
    overflow: hidden;
    background: var(--card-white);
    box-shadow: 0 10px 30px rgba(0,0,0,0.18);
  }
  .card-art { position: absolute; inset: 0; }
  .brand {
    position: absolute;
    left: 70px;
    top: 80px;
    display: flex;
    align-items: center;
    gap: 22px;
  }
  .brand-dot {
    width: 62px;
    height: 62px;
    border-radius: 50%;
    background: var(--red);
  }
  .brand-name {
    font-family: "Questrial", sans-serif;
    font-size: 52px;
    line-height: 1;
    color: var(--navy);
  }
  .contact {
    position: absolute;
    right: 52px;
    top: 226px;
    text-align: right;
    font-family: "Questrial", sans-serif;
    color: var(--text-light);
  }
  .person-name {
    font-family: "Kalam", cursive;
    font-size: 40px;
    color: var(--gold-light);
    margin: 0;
    line-height: 1.1;
  }
  .person-role {
    font-family: "Kalam", cursive;
    font-size: 27px;
    color: #ffffff;
    margin: 2px 0 22px;
    line-height: 1.1;
  }
  .address { font-size: 27px; line-height: 1.2; margin: 0 0 24px; }
  .contact-line {
    display: flex;
    justify-content: flex-end;
    align-items: center;
    gap: 10px;
    font-size: 27px;
    line-height: 38px;
  }
  .contact-line svg { width: 24px; height: 24px; fill: var(--gold); }
  .social {
    position: absolute;
    left: 62px;
    bottom: 36px;
    display: flex;
    gap: 10px;
  }
  .social span {
    width: 26px;
    height: 26px;
    border-radius: 50%;
    border: 2px solid var(--gold);
    box-sizing: border-box;
  }
</style>
</head>
<body>
  <div class="business-card">
    <svg class="card-art" viewBox="0 0 1000 568" preserveAspectRatio="none" aria-hidden="true">
      <defs>
        <linearGradient id="navyFill" x1="0" y1="0" x2="1" y2="1">
          <stop offset="0" stop-color="#1d2a5c"/>
          <stop offset="1" stop-color="#0d1535"/>
        </linearGradient>
        <linearGradient id="goldFill" x1="0" y1="0" x2="1" y2="0">
          <stop offset="0" stop-color="#e8b40f"/>
          <stop offset="1" stop-color="#fbd022"/>
        </linearGradient>
      </defs>
      <!-- gold ribbon -->
      <path d="M560 232 C690 150 840 118 1000 112 L1000 142 C840 148 700 176 600 232 Z" fill="url(#goldFill)"/>
      <!-- navy wave -->
      <path d="M0 470 C180 480 340 430 470 300 C560 210 720 150 1000 136 L1000 568 L0 568 Z" fill="url(#navyFill)"/>
      <!-- red swoosh -->
      <path d="M0 338 C100 392 250 422 400 402 C260 440 110 420 0 364 Z" fill="var(--red)"/>
    </svg>

    <div class="brand">
      <span class="brand-dot"></span>
      <span class="brand-name">Summit Ridge Garlic</span>
    </div>

    <div class="contact">
      <p class="person-name">Dale Harper</p>
      <p class="person-role">CEO/Founder</p>
      <p class="address">P.O. Box 12<br>Elbert, CO&nbsp;&nbsp;80106</p>
      <div class="contact-line">719-555-0142
        <svg viewBox="0 0 24 24"><path d="M6.6 10.8a15.1 15.1 0 0 0 6.6 6.6l2.2-2.2c.3-.3.7-.4 1-.2 1.1.4 2.3.6 3.6.6.6 0 1 .4 1 1V20c0 .6-.4 1-1 1A17 17 0 0 1 3 4c0-.6.4-1 1-1h3.5c.6 0 1 .4 1 1 0 1.3.2 2.5.6 3.6.1.3 0 .7-.2 1z"/></svg>
      </div>
      <div class="contact-line">hello@RidgeGarlic.com
        <svg viewBox="0 0 24 24"><path d="M2 5h20v14H2z M3.5 6.5 12 13l8.5-6.5" fill="var(--gold)" stroke="var(--navy)" stroke-width="1.5"/></svg>
      </div>
      <div class="contact-line">www.RidgeGarlic.com
        <svg viewBox="0 0 24 24"><circle cx="12" cy="12" r="10" fill="var(--gold)"/><path d="M2 12h20M12 2c3 3 3 17 0 20M12 2c-3 3-3 17 0 20" fill="none" stroke="var(--navy)" stroke-width="1.3"/></svg>
      </div>
    </div>

    <div class="social" aria-label="Social media links">
      <span></span><span></span><span></span><span></span>
    </div>
  </div>
</body>
</html>
```